Residential Mortgage Leader needs Wordpress Design

Looking for a home page website design for a client. We develop using the WordPress platform and would prefer the design be at least loosely based on an existing WordPress template. Attached files have many notes from our creative brief with client. The site must be responsive. Approved, basic wireframe attached. There is room for interpretation.

Existing web site: http://www.marisolkettering.example/

The Marisol Kettering Team relies on strong systems to deliver an on-time, done-right, friendly experience. Marisol offers mortgages and refinancing services throughout the United States. She is a successful Brookvale Funding agent who strives to be an active part of her community. She would like to focus the site on her team, rather than just her.

Difference makers...
When you work with the Marisol Kettering team you get a high level of expertise and a friendly experience.

She has amazing credentials. Marisol is widely recognized as a top producer for her company, and has earned a number of awards and honors for her customer service.

Marisol's team is very engaged and enjoys sharing social comments or photos from their community.

Imagery:
* Friendly, warm imagery, preferably of her team or an image to represent her team
* Clean and crisp
* Professional / Experts in mortgage and refinance
* Clean / Good use of white space
Updates

When possible, please use imagery from the DFW area. The client mentioned they would prefer not to see stock images. Thanks.

Amend that- creative use of stock images, however, is fine. A few designs have used stock imagery, but in a well-considered manner.

We added some photos and graphics that are local. We are Dallas / Ft. Worth, Plano, Frisco, Texas. We also added some examples of photos to use for the "In the Community" area. Stock photos of business folks just doesn't fit there. Thanks!

Target Market(s)

They service a lot of builders, but also work with homeowners. Their typical client is usually a woman searching for mortgage services online. She typically has a family and may refer her husband to Marisol's team. Keep in mind, however, they also see a number of other scenarios. Most of their clients are middle to high-end borrowers.

Industry/Entity Type

It Company

Requirements
Must have
• Design should be developed using program such as Photoshop or Fireworks or Illustrator as last preference. Ideally, the design would be based on an existing responsive WordPress theme, which we would customize. You must include the name of the target theme. The footer should include lots of space for disclaimers and legal language. Site navigation should include these choices: "Home, About, Builders, Mortgage Info, Approval, Blog, Contact"
Nice to have
• Blog, social media and photos area. Use of the already approved style prototype with colors and fonts (Lato- a Google font, Times New Roman and Cookie-a decorative Google font). However, we are open to interpretation.
Should not have
• Hard to read fonts or a lack of white space.

```html
<!DOCTYPE html>
<html lang="en">
<head>
<meta charset="utf-8">
<title>Brookvale Funding – Marisol Kettering Team</title>
<link href="https://fonts.googleapis.com/css2?family=PT+Sans:wght@400;700&family=PT+Sans+Narrow:wght@700&family=Parisienne&display=swap" rel="stylesheet">
<style>
:root{
  --red:#c4301f;
  --red-light:#d8402c;
  --ink:#3a3a3a;
  --muted:#555;
  --grey-btn:#8c8c8c;
  --panel:rgba(40,40,40,.78);
  --rule:#e2e2e2;
  --footer:#f0f0f0;
}
*{margin:0;padding:0;box-sizing:border-box}
html,body{width:972px;height:1200px;overflow:hidden;background:#fff}
body{font-family:"PT Sans",sans-serif;color:var(--ink)}
.page{position:relative;width:972px;height:1200px;overflow:hidden}
.abs{position:absolute}
.script{font-family:"Parisienne",cursive;font-weight:400;color:#222}
.hero-bg{left:0;top:0;width:972px;height:502px;background:linear-gradient(180deg,#f4f4f4 0%,#d9d9d9 22%,#9a9a9a 55%,#5e5e5e 100%)}
.brand{left:92px;top:34px;font-size:34px;font-weight:700;color:var(--red);letter-spacing:-.5px}
.brand-sub{left:93px;top:76px;font-size:17px;color:#555}
.search{left:521px;top:52px;width:177px;height:28px;background:#fff;border:1px solid #ccc;border-radius:3px;font-size:9px;color:#666;padding:8px 0 0 13px}
.search svg{position:absolute;right:10px;top:7px}
.contact{left:713px;top:22px;color:var(--red)}
.contact .lbl{font-size:15px}
.contact .phone{font-size:25px;line-height:1.1}
.contact .mail{font-size:12px}
.nav{left:82px;top:111px;width:810px;height:42px;background:var(--red);display:flex;padding-left:112px}
.nav a{color:#fff;text-decoration:none;font-size:15px;line-height:42px;padding:0 13px;margin-right:4px}
.nav a.active{background:#333}
.team-name{left:662px;top:160px;font-size:36px;color:var(--red);letter-spacing:-.5px}
.team-sub{left:725px;top:201px;font-size:10.5px;color:#777;letter-spacing:.8px}
.photo{border:5px solid #fff;box-shadow:0 2px 6px rgba(0,0,0,.35)}
.arrow{width:24px;height:24px;border-radius:50%;background:#333;top:438px}
.panel{left:492px;top:251px;width:370px;height:211px;background:var(--panel);color:#fff}
.panel h1{position:absolute;left:34px;top:22px;font-family:"Parisienne",cursive;font-weight:400;font-size:30px;color:#fff}
.panel p{position:absolute;left:36px;top:68px;width:286px;font-size:15.5px;line-height:1.25}
.btn{top:158px;height:28px;color:#fff;font-size:15px;text-align:center;line-height:28px;border-radius:2px}
.btn-red{left:38px;width:104px;background:var(--red-light)}
.btn-grey{left:188px;width:137px;background:var(--grey-btn)}
.or{left:156px;top:160px;font-size:14px}
.col-rule{width:1px;background:linear-gradient(180deg,transparent,#e6e6e6,transparent)}
.h-script{font-size:32px}
.body-text{font-size:11px;line-height:1.25;color:var(--muted)}
.red-sub{font-size:13px;color:var(--red)}
ul.dots{list-style:none}
ul.dots li{position:relative;padding-left:15px;color:var(--muted)}
ul.dots li::before{content:"";position:absolute;left:2px;top:.55em;width:5px;height:5px;border-radius:50%;background:var(--red)}
.hrule{left:0;width:972px;height:1px;background:var(--rule)}
.narrow{font-family:"PT Sans Narrow",sans-serif;font-weight:700;font-size:23px;color:#222}
.social{left:369px;top:806px}
.social div{display:flex;align-items:center;height:31px;font-size:14px;color:#444}
.social i{display:inline-block;width:24px;height:24px;margin-right:12px}
.person{width:61px;height:61px;border:3px solid #fff;box-shadow:0 0 2px rgba(0,0,0,.3);background:linear-gradient(180deg,#c9c4bd,#8a7f76)}
.pname{font-size:9.5px;color:#333;width:80px;text-align:center}
.footer{left:0;top:980px;width:972px;height:220px;background:linear-gradient(180deg,#fafafa,var(--footer))}
.ft{font-size:11px;line-height:14.6px;color:#444}
.contact-col{width:148px;white-space:nowrap}
.lang{left:649px;top:1085px;width:163px;height:28px;background:#fff;border:1px solid #e4e4e4;font-size:11px;color:#aaa;padding:7px 0 0 12px}
</style>
</head>
<body>
<div class="page">
  <div class="abs hero-bg" role="img" aria-label="Black and white panorama of a city skyline"></div>

  <div class="abs brand">Brookvale Funding</div>
  <div class="abs brand-sub">A Ridgeline Capital Company</div>

  <div class="abs search">Search
    <svg width="14" height="14" viewBox="0 0 14 14"><circle cx="6" cy="6" r="4.5" fill="none" stroke="#777" stroke-width="1.4"/><line x1="9.3" y1="9.3" x2="13" y2="13" stroke="#777" stroke-width="1.6"/></svg>
  </div>

  <div class="abs contact">
    <div class="lbl">Work with us :</div>
    <div class="phone">214 - 555 - 0136</div>
    <div class="mail">Email : info@brookvalefunding.example</div>
  </div>

  <nav class="abs nav">
    <a class="active" href="#">Home</a><a href="#">About Us</a><a href="#">Business</a><a href="#">Manage info</a><a href="#">Approval</a><a href="#">Blog</a><a href="#">Contact Us</a>
  </nav>

  <div class="abs team-name">marisolkettering</div>
  <div class="abs team-sub">THE MARISOL KETTERING TEAM</div>

  <div class="abs photo" style="left:117px;top:176px;width:201px;height:132px;background:linear-gradient(180deg,#9fc2e6,#c6743f 55%,#8a9a5a)" role="img" aria-label="Historic red-roofed depot building"></div>
  <div class="abs photo" style="left:228px;top:240px;width:192px;height:126px;transform:rotate(-24deg);background:linear-gradient(180deg,#cfe0ee,#9aa4ad)" role="img" aria-label="Town centre buildings with towers"></div>
  <div class="abs photo" style="left:120px;top:315px;width:196px;height:136px;transform:rotate(28deg);background:linear-gradient(180deg,#2d4fa0 45%,#8e8e8e)" role="img" aria-label="Large retail store with parked cars"></div>

  <div class="abs arrow" style="left:100px"><svg width="24" height="24"><path d="M14 7 L9 12 L14 17Z" fill="#fff"/></svg></div>
  <div class="abs arrow" style="left:130px"><svg width="24" height="24"><path d="M10 7 L15 12 L10 17Z" fill="#fff"/></svg></div>

  <section class="abs panel">
    <h1>Earning Your Business</h1>
    <p>The Marisol Kettering Team relies on strong systems to deliver an on-time, done-right and friendly experience</p>
    <div class="abs btn btn-red">Start here</div>
    <div class="abs or">(Or)</div>
    <div class="abs btn btn-grey">Get to know us</div>
  </section>

  <div class="abs col-rule" style="left:346px;top:505px;height:170px"></div>
  <div class="abs col-rule" style="left:608px;top:505px;height:170px"></div>

  <h2 class="abs script h-script" style="left:93px;top:520px">Our Credentials</h2>
  <div class="abs red-sub" style="left:94px;top:564px">A top-producer , top-notch</div>
  <p class="abs body-text" style="left:94px;top:591px;width:200px">Lorem Ipsum is simply dummy text of the printing and typesetting industry. Lorem Ipsum has been the industry's standard dummy text ever</p>

  <h2 class="abs script h-script" style="left:377px;top:520px">Awards</h2>
  <ul class="abs dots body-text" style="left:378px;top:572px;line-height:16.2px">
    <li>Sed ut perspiciatis</li><li>Neque porro quisquam est,</li><li>Nam libero tempore, cum soluta nobis</li><li>The wise man therefore always</li>
  </ul>

  <h2 class="abs script h-script" style="left:636px;top:520px">Recognition</h2>
  <p class="abs body-text" style="left:636px;top:584px;width:200px">Lorem Ipsum is simply dummy text of the printing and typesetting industry. Lorem Ipsum has been the industry's standard dummy text ever</p>

  <div class="abs hrule" style="top:679px"></div>

  <h2 class="abs script" style="left:0;width:972px;text-align:center;top:692px;font-size:30px">Engaged in our Community</h2>
  <div class="abs red-sub" style="left:0;width:972px;text-align:center;top:734px;font-size:12px">Connect with us</div>

  <div class="abs col-rule" style="left:346px;top:760px;height:215px"></div>
  <div class="abs col-rule" style="left:608px;top:760px;height:215px"></div>

  <h3 class="abs narrow" style="left:94px;top:768px">Blog</h3>
  <ul class="abs dots" style="left:94px;top:810px;font-size:12.5px;line-height:19.4px">
    <li>Borrowing</li><li>Best Practices</li><li>Announcements</li><li>Resources</li><li>How to guides</li><li>Builders info</li>
  </ul>

  <h3 class="abs narrow" style="left:370px;top:768px">Social</h3>
  <div class="abs social">
    <div><i style="background:#2f55a4"></i>Facebook</div>
    <div><i style="background:#38a9e0"></i>Twitter</div>
    <div><i style="background:#555"></i>Google plus</div>
    <div><i style="background:#f39a1d"></i>Rss feed</div>
  </div>

  <h3 class="abs narrow" style="left:646px;top:768px">In the community</h3>
  <div class="abs person" style="left:648px;top:806px" role="img" aria-label="Portrait of a community team member"></div>
  <div class="abs person" style="left:736px;top:806px" role="img" aria-label="Portrait of a community team member"></div>
  <div class="abs person" style="left:648px;top:889px" role="img" aria-label="Portrait of a community team member"></div>
  <div class="abs person" style="left:736px;top:889px" role="img" aria-label="Portrait of a community team member"></div>
  <div class="abs pname" style="left:638px;top:869px">Person Name</div>
  <div class="abs pname" style="left:726px;top:869px">Person Name</div>
  <div class="abs pname" style="left:638px;top:952px">Person Name</div>
  <div class="abs pname" style="left:726px;top:952px">Person Name</div>

  <footer class="abs footer"></footer>
  <div class="abs hrule" style="top:980px"></div>
  <div class="abs col-rule" style="left:346px;top:985px;height:190px"></div>
  <div class="abs col-rule" style="left:608px;top:985px;height:190px"></div>

  <div class="abs photo" style="left:93px;top:1012px;width:81px;height:90px;border-width:5px;background:linear-gradient(180deg,#6a5646,#b88f74)" role="img" aria-label="Portrait of Marisol Kettering"></div>
  <div class="abs" style="left:97px;top:1112px;font-size:12.5px;color:#222">Marisol Kettering</div>
  <div class="abs ft" style="left:97px;top:1130px;font-size:10.5px;line-height:13px">Branch Manager<br>NMLS #: 40512</div>
  <div class="abs ft contact-col" style="left:192px;top:1018px">Office: 469.555.0142<br>Cell: 866.555.0177<br>mkettering@brookvale.example</div>
  <div class="abs ft contact-col" style="left:192px;top:1076px">4820 Cedar Commons , Ste. 210<br>Frisco, TX 75036</div>

  <h4 class="abs" style="left:373px;top:1000px;font-size:19px;font-weight:400;color:#555">Head office</h4>
  <svg class="abs" style="left:563px;top:1002px" width="16" height="12"><path d="M6 1 L1 6 L6 11Z M10 1 L15 6 L10 11Z" fill="#777"/></svg>
  <div class="abs ft" style="left:373px;top:1033px">Our Address<br>Corporate Office - 2250 Elmridge Parkway,<br>Suite 600 Dallas, Texas 75201<br>Tel : 1-800-555-0199<br>Email : Contact Brookvale Funding</div>

  <div class="abs" style="left:680px;top:999px;width:75px;height:78px;background:#888;border-radius:4px" role="img" aria-label="Equal housing badge"></div>
  <div class="abs lang">Languages
    <svg class="abs" style="left:120px;top:7px" width="20" height="13"><rect width="20" height="13" fill="#c33"/><rect y="2" width="20" height="2" fill="#fff"/><rect y="6" width="20" height="2" fill="#fff"/><rect y="10" width="20" height="2" fill="#fff"/><rect width="9" height="7" fill="#2c3e8c"/></svg>
    <svg class="abs" style="left:147px;top:11px" width="10" height="6"><path d="M0 0 L10 0 L5 6Z" fill="#999"/></svg>
  </div>
  <div class="abs ft" style="left:654px;top:1129px">© 2013.www.brookvalefunding.example</div>
  <div class="abs ft" style="left:904px;top:1129px">M1</div>
</div>
</body>
</html>
```